Non Profit Company Looking For New Website

The website for Fernvale Quillstone Heritage Society should offer the viewer beautiful photos that inspire condifence and joy and tap into our love of horses.

We would like to see a website that displays trust, quality and confidence. Needs to be responsive and mobile friendly for all browsers and coded for both Android & IOS.

READ ATTACHED WEBSITE TEMPLATE FOR COMPLETE DETAILS ON WHAT WE ARE LOOKING FOR.

Looking for recommmendations if we should use WordPress/WooCommerce for site or Wordpress with Shopify Plug in or just Shopify.

Must be both desktop and mobile friendly with fast page load speed. Need the ability to edit ourselves.

Industry/Entity Type

Non Profit

Coding

Coded - Design and coding required

Number of Pages Required

5+ page

Requirements
Must have
• We would like to see a website that displays trust, quality and confidence. Needs to be responsive and mobile friendly for all browsers and coded for both Android & IOS.

Looking for recommendations if we should use WordPress/WooCommerce for site or Wordpress with Shopify Plug in or just Shopify.

Logo Colour:
Pantone 7621 C

READ TEMPLATE THAT IS ATTACHED
Nice to have
• Like look of this website as a sample:
https://www.quellbrimtorva.com/

Another similar non profit organization
https://pellaworthcindle.com/

```html
<!DOCTYPE html>
<html lang="en">
<head>
<meta charset="utf-8">
<title>Fernvale Quillstone Heritage Society</title>
<link rel="stylesheet" href="https://fonts.googleapis.com/css2?family=Cinzel:wght@400;700&family=Roboto:wght@400;500;700&display=swap">
<style>
:root{
  --red:#c41e2e;
  --red-dark:#a8161f;
  --ink:#111111;
  --text:#444444;
  --grey-bg:#f2f2f2;
  --white:#ffffff;
  --line:#dddddd;
  --footer:#0a0a0a;
}
*{margin:0;padding:0;box-sizing:border-box}
html,body{width:1200px;height:3539px;overflow:hidden}
body{position:relative;background:var(--white);font-family:'Roboto',Arial,sans-serif;color:var(--text)}
.abs{position:absolute}
.serif{font-family:'Cinzel',Georgia,serif}

/* header */
.site-header{left:0;top:0;width:1200px;height:83px;background:var(--white);z-index:5}
.brand-tab{left:76px;top:0;width:182px;height:133px;z-index:6}
.brand-name{left:76px;top:8px;width:182px;text-align:center;color:var(--red);font-family:'Cinzel',Georgia,serif;font-weight:400;line-height:1.1;z-index:7}
.brand-name .big{display:block;font-size:21px;letter-spacing:1px}
.brand-name .small{display:block;font-size:11.5px;margin-top:6px}
.main-nav{left:364px;top:29px;display:flex;gap:23px;font-size:15px;font-weight:500;color:var(--ink);z-index:7}
.main-nav .active{color:var(--red)}
.social{display:flex;gap:11px}
.social span{width:36px;height:36px;border-radius:50%;display:block}
.social-top{left:957px;top:21px;z-index:7}
.social-top span{border:2px solid #e8e8e8;background:var(--white)}
.social-top span:first-child{background:var(--red);border-color:var(--red)}

/* hero */
.hero-photo{left:0;top:83px;width:1200px;height:690px;background:linear-gradient(100deg,#7d6a45 0%,#b99c63 35%,#a8854f 55%,#6e4a2c 75%,#c4a670 100%)}
.hero-title{left:110px;top:276px;font-size:37px;font-weight:700;color:var(--white);letter-spacing:1px}
.hero-sub{left:110px;top:333px;font-size:16.5px;font-weight:700;color:var(--white);line-height:27px}
.btn-solid{background:var(--red);color:var(--white);border-radius:26px;font-size:15px;font-weight:700;display:flex;align-items:center;justify-content:center}
.hero-btn{left:110px;top:408px;width:154px;height:50px}
.hero-wave{left:0;top:560px;width:1200px;height:220px}

/* about */
.section-title{width:1200px;left:0;text-align:center;color:var(--ink);font-family:'Cinzel',Georgia,serif;font-weight:700}
.about-title{top:844px;font-size:28px}
.about-text{left:140px;width:920px;top:919px;text-align:center;font-size:15.5px;line-height:26px;color:#555}
.btn-outline{border:2px solid var(--red);color:var(--red);border-radius:26px;font-size:14.5px;font-weight:500;display:flex;align-items:center;justify-content:center;background:transparent}
.about-btn{left:492px;top:1028px;width:215px;height:48px}

/* adopt */
.adopt-band{left:0;top:1210px;width:1200px;height:846px;background:var(--grey-bg)}
.adopt-title{top:1254px;font-size:38px}
.adopt-sub{left:0;width:1200px;top:1333px;text-align:center;font-size:15px;color:#555}
.horse-card{width:318px;height:251px;border-bottom:3px solid var(--red)}
.horse-a{background:linear-gradient(180deg,#4f7a3a 0%,#6b8f45 55%,#5e8a35 100%)}
.horse-b{background:linear-gradient(180deg,#3f6a34 0%,#8a6d4a 55%,#6e8a3f 100%)}
.horse-c{background:linear-gradient(180deg,#2f4a2a 0%,#5a4a30 55%,#708a4a 100%)}
.horse-d{background:linear-gradient(180deg,#3f6f2c 0%,#a0653a 55%,#4f8a35 100%)}
.horse-e{background:linear-gradient(180deg,#2f5a2a 0%,#8c6440 55%,#5e7a3a 100%)}
.horse-f{background:linear-gradient(180deg,#6b7a8c 0%,#a86a3e 55%,#58703e 100%)}
.adopt-btn{left:532px;top:1952px;width:136px;height:50px}

/* difference */
.give-photo{left:0;top:2056px;width:1200px;height:434px;background:linear-gradient(90deg,#d88a3a 0%,#e8a865 25%,#a85a2c 50%,#6a3a1e 75%,#4a2a18 100%)}
.give-title{left:625px;width:468px;top:2124px;text-align:center;font-size:30px;font-weight:700;color:var(--white);font-family:'Cinzel',Georgia,serif}
.give-rule{left:777px;top:2171px;width:162px;height:3px;background:var(--white)}
.give-text{left:620px;width:478px;top:2203px;text-align:center;font-size:14.5px;line-height:26px;color:var(--white)}
.give-btn{left:760px;top:2363px;width:196px;height:49px;border:2px solid var(--white);color:var(--white);font-weight:700;border-radius:26px;font-size:14.5px;display:flex;align-items:center;justify-content:center}

/* contact */
.contact-title{top:2574px;font-size:38px}
.contact-rule{left:516px;top:2625px;width:169px;height:3px;background:var(--red)}
.info-icon{width:64px;height:64px}
.info-label{left:221px;font-size:17px;color:var(--red);font-weight:500}
.info-text{left:221px;font-size:15px;line-height:24px;color:var(--ink)}
.field{border:2px solid #e6e6e6;border-radius:6px;background:var(--white);font-size:14.5px;color:#666;display:flex;align-items:center;padding-left:16px;gap:8px;box-shadow:0 1px 3px rgba(0,0,0,.06)}
.field.area{align-items:flex-start;padding-top:14px}
.field svg{flex:none}
.submit-btn{left:499px;top:2963px;width:153px;height:50px;gap:12px}

/* footer */
.footer-wave{left:0;top:3100px;width:1200px;height:439px}
.footer-brand{left:110px;top:3314px;width:162px;text-align:center;color:var(--red);font-family:'Cinzel',Georgia,serif;font-weight:400;line-height:1.15}
.footer-brand .big{display:block;font-size:29px}
.footer-brand .small{display:block;font-size:17px;margin-top:16px}
.footer-divider{top:3318px;width:1px;height:148px;background:#444}
.footer-head{top:3316px;font-size:17px;font-weight:700;color:var(--white)}
.footer-list{list-style:none;font-size:15px;color:var(--white);line-height:25.5px}
.footer-contact{left:891px;top:3352px;list-style:none;font-size:15px;color:var(--white)}
.footer-contact li{display:flex;gap:16px;line-height:25px;margin-bottom:8px}
.footer-contact svg{flex:none;margin-top:6px}
.footer-rule{left:110px;top:3483px;width:978px;height:1px;background:#444}
.copyright{left:110px;top:3504px;font-size:12px;color:var(--white)}
.copyright em{font-style:normal;color:var(--red)}
.social-foot{left:968px;top:3494px}
.social-foot span{background:var(--white)}
</style>
</head>
<body>

<!-- header -->
<header class="abs site-header" role="banner"></header>
<svg class="abs brand-tab" viewBox="0 0 182 133" aria-hidden="true"><path d="M0 0 H182 V83 L158 133 H24 L0 83 Z" fill="#ffffff"/></svg>
<div class="abs brand-name"><span class="big">FERNVALE</span><span class="small">QUILLSTONE<br>HERITAGE SOCIETY</span></div>
<nav class="abs main-nav">
  <span class="active">HOME</span><span>ABOUT</span><span>ADOPT</span><span>HORSES</span><span>DONATE/SHOP</span><span>CONTACT</span>
</nav>
<div class="abs social social-top" aria-label="Social links"><span></span><span></span><span></span></div>

<!-- hero -->
<div class="abs hero-photo" role="img" aria-label="Rider in helmet on a bay horse beside a fence in a golden field"></div>
<h1 class="abs hero-title serif">RETIRE. RETRAIN. REHOME.</h1>
<p class="abs hero-sub">We support and develop retired thoroughbred racehorses<br>for their next chapter in life</p>
<div class="abs btn-solid hero-btn">LEARN MORE</div>
<svg class="abs hero-wave" viewBox="0 0 1200 220" preserveAspectRatio="none" aria-hidden="true">
  <path d="M0 148 C110 80 210 40 330 45 C520 55 760 200 960 203 C1060 205 1140 170 1200 128 L1200 220 L0 220 Z" fill="#c41e2e"/>
  <path d="M0 160 C110 95 210 58 330 62 C520 72 760 210 960 214 C1060 216 1140 182 1200 142 L1200 220 L0 220 Z" fill="#ffffff"/>
</svg>

<!-- about -->
<h2 class="abs section-title about-title">WHAT IS THOROUGHBRED AFTERCARE?</h2>
<p class="abs about-text">The health, safety and welfare of our equine athletes does not end at the finish line, and retirement and aftercare are critical to the success of the racing industry. Aftercare is the safe placement of racehorses after their careers as racehorse are completed. Some horses might retire to the breeding shed or broodmare bands, while others are retrained for second careers.</p>
<div class="abs btn-outline about-btn">LEARN MORE ABOUT US</div>

<!-- adopt -->
<section class="abs adopt-band"></section>
<h2 class="abs section-title adopt-title">ADOPT A HORSE</h2>
<p class="abs adopt-sub">Fernvale Quillstone Heritage Society is committed to helping match you with the perfect horse.</p>
<div class="abs horse-card horse-a" style="left:110px;top:1389px" role="img" aria-label="Dark bay horse standing on green grass"></div>
<div class="abs horse-card horse-b" style="left:440px;top:1389px" role="img" aria-label="Chestnut horse standing in front of trees"></div>
<div class="abs horse-card horse-c" style="left:770px;top:1389px" role="img" aria-label="Bay horse standing in a paddock"></div>
<div class="abs horse-card horse-d" style="left:110px;top:1654px" role="img" aria-label="Chestnut horse in bridle on a lawn"></div>
<div class="abs horse-card horse-e" style="left:440px;top:1654px" role="img" aria-label="Brown horse in front of hedges"></div>
<div class="abs horse-card horse-f" style="left:770px;top:1654px" role="img" aria-label="Chestnut horse among flowering shrubs"></div>
<div class="abs btn-outline adopt-btn">ADOPT NOW</div>

<!-- make a difference -->
<div class="abs give-photo" role="img" aria-label="Woman leaning against a white horse at sunset"></div>
<h2 class="abs give-title">MAKE A DIFFERENCE</h2>
<div class="abs give-rule"></div>
<p class="abs give-text">Lorem ipsum dolor sit amet, consectetur adipiscing elit, sed do eiusmod tempor incididunt ut labore et dolore magna aliqua. Ut enim ad minim veniam, quis nostrud exercitation ullamco laboris nisi ut aliquip ex ea commodo consequat. Duis aute irure dolor in reprehenderit in voluptate velit esse cillum dolore eu.</p>
<div class="abs give-btn">MORE WAYS TO GIVE</div>

<!-- contact -->
<h2 class="abs section-title contact-title">GET IN TOUCH</h2>
<div class="abs contact-rule"></div>

<svg class="abs info-icon" style="left:133px;top:2678px" viewBox="0 0 64 64" aria-hidden="true">
  <circle cx="32" cy="32" r="30" fill="none" stroke="#c41e2e" stroke-width="2.5"/>
  <path d="M32 46 C26 38 22 32 22 27 a10 10 0 0 1 20 0 c0 5 -4 11 -10 19z" fill="none" stroke="#c41e2e" stroke-width="2"/>
  <circle cx="32" cy="27" r="3.5" fill="none" stroke="#c41e2e" stroke-width="2"/>
</svg>
<div class="abs info-label" style="top:2674px">LOCATION</div>
<div class="abs info-text" style="top:2704px">123, Lorem ipsum dolor,<br>United States</div>

<svg class="abs info-icon" style="left:133px;top:2769px" viewBox="0 0 64 64" aria-hidden="true">
  <circle cx="32" cy="32" r="30" fill="none" stroke="#c41e2e" stroke-width="2.5"/>
  <path d="M22 20 l5 -2 l4 8 l-3 3 c2 4 5 7 9 9 l3 -3 l8 4 l-2 5 c-12 0 -24 -12 -24 -24z" fill="none" stroke="#c41e2e" stroke-width="2" stroke-linejoin="round"/>
</svg>
<div class="abs info-label" style="top:2775px">CALL US</div>
<div class="abs info-text" style="top:2805px">123-456-7890</div>

<svg class="abs info-icon" style="left:133px;top:2858px" viewBox="0 0 64 64" aria-hidden="true">
  <circle cx="32" cy="32" r="30" fill="none" stroke="#c41e2e" stroke-width="2.5"/>
  <rect x="17" y="22" width="30" height="20" fill="none" stroke="#c41e2e" stroke-width="2"/>
  <path d="M17 22 L32 34 L47 22 M17 42 L27 31 M47 42 L37 31" fill="none" stroke="#c41e2e" stroke-width="2"/>
</svg>
<div class="abs info-label" style="top:2864px">EMAIL US</div>
<div class="abs info-text" style="top:2894px">info@fernvalequillstone.org</div>

<div class="abs field" style="left:499px;top:2678px;width:289px;height:51px">
  <svg width="12" height="13" viewBox="0 0 12 13" aria-hidden="true"><circle cx="6" cy="3.5" r="3" fill="#777"/><path d="M0 13 c0-5 2-7 6-7 s6 2 6 7z" fill="#777"/></svg>First Name</div>
<div class="abs field" style="left:799px;top:2678px;width:289px;height:51px">
  <svg width="12" height="13" viewBox="0 0 12 13" aria-hidden="true"><circle cx="6" cy="3.5" r="3" fill="#777"/><path d="M0 13 c0-5 2-7 6-7 s6 2 6 7z" fill="#777"/></svg>Last Name</div>
<div class="abs field" style="left:499px;top:2744px;width:289px;height:51px">
  <svg width="12" height="12" viewBox="0 0 12 12" aria-hidden="true"><path d="M1 2 l3-1 l2 3 l-2 1.5 c1 2 2 3 3.5 3.5 l1.5-2 l3 2 l-1 3 c-6 0-12-6-12-10z" fill="#777"/></svg>Your Phone</div>
<div class="abs field" style="left:799px;top:2744px;width:289px;height:51px">
  <svg width="14" height="11" viewBox="0 0 14 11" aria-hidden="true"><rect x="0.75" y="0.75" width="12.5" height="9.5" fill="none" stroke="#777" stroke-width="1.5"/><path d="M1 1 L7 6 L13 1" fill="none" stroke="#777" stroke-width="1.5"/></svg>Your Email</div>
<div class="abs field area" style="left:499px;top:2810px;width:589px;height:114px">
  <svg width="13" height="12" viewBox="0 0 13 12" aria-hidden="true" style="margin-top:3px"><ellipse cx="6.5" cy="5" rx="6.5" ry="4.8" fill="#777"/><path d="M2 8 L1 12 L5 9z" fill="#777"/></svg>How Can we hel you?</div>
<div class="abs btn-solid submit-btn">SUBMIT
  <svg width="16" height="14" viewBox="0 0 16 14" aria-hidden="true"><path d="M0 7 L16 0 L12 14 L7 10 L14 2 L5 9z" fill="#ffffff"/></svg></div>

<!-- footer -->
<svg class="abs footer-wave" viewBox="0 0 1200 439" preserveAspectRatio="none" aria-hidden="true">
  <path d="M0 87 C110 40 200 8 320 10 C560 14 820 175 1000 172 C1090 170 1160 110 1200 62 L1200 439 L0 439 Z" fill="#c41e2e"/>
  <path d="M0 112 C110 68 200 38 320 40 C560 46 820 200 1000 196 C1090 194 1160 134 1200 88 L1200 439 L0 439 Z" fill="#0a0a0a"/>
</svg>
<div class="abs footer-brand"><span class="big">FERNVALE</span><span class="small">QUILLSTONE<br>HERITAGE<br>SOCIETY</span></div>
<div class="abs footer-divider" style="left:323px"></div>
<div class="abs footer-divider" style="left:565px"></div>
<div class="abs footer-divider" style="left:807px"></div>

<div class="abs footer-head" style="left:384px">QUICK LINKS</div>
<ul class="abs footer-list" style="left:384px;top:3353px"><li>Home</li><li>About</li><li>Adopt</li><li>Horses</li></ul>
<div class="abs footer-head" style="left:637px">ABOUT</div>
<ul class="abs footer-list" style="left:637px;top:3353px"><li>Donate/Shop</li><li>Site Map</li><li>Privacy Policy</li><li>Terms Of Use</li></ul>
<div class="abs footer-head" style="left:891px">CONTACT US</div>
<ul class="abs footer-contact" style="left:891px">
  <li><svg width="10" height="13" viewBox="0 0 10 13" aria-hidden="true"><path d="M5 13 C2 9 0 7 0 5 a5 5 0 0 1 10 0 c0 2-2 4-5 8z" fill="#c41e2e"/><circle cx="5" cy="5" r="1.8" fill="#0a0a0a"/></svg><span>123, Lorem ipsum dolor,<br>United States</span></li>
  <li><svg width="12" height="12" viewBox="0 0 12 12" aria-hidden="true"><path d="M1 2 l3-1 l2 3 l-2 1.5 c1 2 2 3 3.5 3.5 l1.5-2 l3 2 l-1 3 c-6 0-12-6-12-10z" fill="#c41e2e"/></svg><span>123-456-7890</span></li>
  <li><svg width="13" height="10" viewBox="0 0 13 10" aria-hidden="true"><rect x="0.75" y="0.75" width="11.5" height="8.5" fill="none" stroke="#c41e2e" stroke-width="1.5"/><path d="M1 1 L6.5 5.5 L12 1" fill="none" stroke="#c41e2e" stroke-width="1.5"/></svg><span>info@fernvalequillstone.org</span></li>
</ul>
<div class="abs footer-rule"></div>
<p class="abs copyright">Copyrights 2021 <em>FERNVALE QUILLSTONE HERITAGE SOCIETY</em>. All rights reserved</p>
<div class="abs social social-foot" aria-label="Social links"><span></span><span></span><span></span></div>

</body>
</html>
```